Business card

We need a business card design for our company based in Auckland , New Zealand called 'Ridge + Studio Ltd'. We provide architectural services. We would like to see designs that use the max. three colours (such as white, black, grey) The final design should communicate financial safety and growth."
Also I will provide our company logo. I would like to the logo to be embeded onto our business card.

Target Market(s)

new residential house, alteration & addition & light commericila design & drafting service

Industry/Entity Type

Architecture

Contact Information for Business Card

Company name: ridge + studio Ltd.
Name: Mark Delford
Job title: architectural designer & Design LBP
email address: mark@rplusd.co.nz
mobile number: 02 5163 2290
web site: www.rplusd.co.nz

Requirements
Must have
• My project must have..
• - embeded logo (attached company logo)
• I don't have a bigger version for our company logo, but I have one old one, so you can remove the word from it)
• - insert the attached small BKTW logo & LBP logo
• - creative, simple and clear business card.
• - Max. three colours
Nice to have
• - Here are the samples I would like to share with you: http://www.plimvora.com/blog/minimalistic-business-card-designs/
• I would like to have my business card like one of the creation.
Should not have
• TBA

```html
<!DOCTYPE html>
<html lang="en">
<head>
<meta charset="utf-8">
<title>Ridge + Studio Ltd — Business Card</title>
<link href="https://fonts.googleapis.com/css2?family=Source+Sans+3:wght@400;600;700&display=swap" rel="stylesheet">
<style>
  :root {
    --stage: #3a3a3c;
    --ink: #0b0b0b;
    --paper: #ffffff;
    --paper-shade: #dcdcdc;
    --grey: #4a4a4a;
    --rule: #9a9a9a;
  }
  * { margin: 0; padding: 0; box-sizing: border-box; }
  html, body {
    width: 1200px;
    height: 950px;
    overflow: hidden;
    background: var(--stage);
    font-family: "Source Sans 3", "Myriad Pro", Arial, sans-serif;
  }
  .canvas {
    width: 1200px;
    height: 950px;
    display: flex;
    flex-direction: column;
    align-items: center;
    justify-content: center;
    gap: 50px;
  }
  .card {
    width: 700px;
    height: 400px;
    position: relative;
    overflow: hidden;
  }

  /* Front */
  .card--front {
    background: var(--ink);
    color: var(--paper);
  }
  .brand {
    position: absolute;
    left: 56px;
    top: 0;
    width: 300px;
    height: 400px;
    display: flex;
    align-items: center;
    gap: 14px;
  }
  .brand__square {
    width: 18px;
    height: 18px;
    background: var(--paper);
    flex: none;
  }
  .brand__name {
    font-size: 34px;
    font-weight: 600;
    letter-spacing: 0.3px;
    color: var(--paper);
    white-space: nowrap;
  }
  .contact {
    position: absolute;
    left: 400px;
    top: 92px;
    line-height: 1.25;
  }
  .contact__name {
    font-size: 30px;
    font-weight: 700;
    text-transform: uppercase;
    letter-spacing: 0.5px;
  }
  .contact__role {
    font-size: 24px;
    font-weight: 400;
  }
  .contact__rule {
    width: 46px;
    height: 2px;
    background: var(--rule);
    margin: 18px 0 16px;
  }
  .contact__company {
    font-size: 20px;
    font-weight: 700;
    margin-bottom: 6px;
  }
  .contact__line {
    font-size: 20px;
    font-weight: 400;
  }

  /* Back */
  .card--back {
    background: linear-gradient(160deg, var(--paper) 0%, #f2f2f2 55%, var(--paper-shade) 100%);
    display: flex;
    align-items: center;
    justify-content: center;
    gap: 34px;
  }
  .partner-name {
    font-size: 64px;
    font-weight: 700;
    color: var(--grey);
    letter-spacing: 1px;
  }
  .partner-divider {
    width: 2px;
    height: 110px;
    background: var(--rule);
  }
  .credential-badge {
    width: 110px;
    height: 110px;
  }
</style>
</head>
<body>
  <main class="canvas">
    <section class="card card--back" aria-label="Business card back">
      <span class="partner-name">BKTW</span>
      <span class="partner-divider"></span>
      <svg class="credential-badge" viewBox="0 0 110 110" role="img" aria-label="Licensed practitioner badge">
        <circle cx="55" cy="55" r="52" fill="var(--grey)"/>
      </svg>
    </section>

    <section class="card card--front" aria-label="Business card front">
      <div class="brand">
        <span class="brand__square" aria-hidden="true"></span>
        <span class="brand__name">ridge + studio</span>
      </div>

      <div class="contact">
        <div class="contact__name">Mark Delford</div>
        <div class="contact__role">architectural designer &amp;<br>Design LBP</div>
        <div class="contact__rule"></div>
        <div class="contact__company">ridge + studio Ltd.</div>
        <div class="contact__line">02 5163 2290</div>
        <div class="contact__line">mark@rplusd.co.nz</div>
        <div class="contact__line">www.rplusd.co.nz</div>
      </div>
    </section>
  </main>
</body>
</html>
```